Meridale Bed Company Needs Business Card

Looking for a very nice looking business card. Creative but not extravagant. We sell beds and pillows across the U.S. and need something professional but catchy. I have attached the logo.

Name : Devin Holt
Title : President
Phone : (800) 471-2960
Email: sleep@quilmora.com
Website: www.quilmora.com

Can be single-sided or double-sided
horizontal or vertical

Can use Blues/Greys

Target Market(s)

Mass Market

Industry/Entity Type

Retail

Contact Information for Business Card

Name : Devin Holt
Title : President
Phone : (800) 471-2960
Email: sleep@quilmora.com
Website: www.quilmora.com

Requirements
Must have
• Clean, Modern, Smooth
• Can use Blues/Greys
• On the other side without the information - have something simple like www.quilmora.com or our logo
Nice to have
• Surprise me
Should not have
• Nothing crazy, nothing cluttered

```html
<!DOCTYPE html>
<html lang="en">
<head>
<meta charset="utf-8">
<title>Quilmora Business Card</title>
<link rel="stylesheet" href="https://fonts.googleapis.com/css2?family=Open+Sans:wght@400;600&display=swap">
<style>
  :root {
    --page-bg: #e9ebee;
    --card-top: #f3f6f8;
    --card-top-edge: #e3e9ee;
    --band-light: #2f86bd;
    --band-dark: #14598e;
    --rule-dark: #2b2d2f;
    --wordmark: #3a4047;
    --text-light: #e4eef6;
    --name-gold: #d8c9a4;
    --icon-light: #d6e3ee;
    --icon-cut: #1f6ea3;
  }
  * { margin: 0; padding: 0; box-sizing: border-box; }
  html, body {
    width: 1200px;
    height: 969px;
    overflow: hidden;
    background: var(--page-bg);
    font-family: "Open Sans", sans-serif;
  }
  .canvas {
    position: relative;
    width: 1200px;
    height: 969px;
  }
  .business-card {
    position: absolute;
    left: 150px;
    top: 228px;
    width: 900px;
    height: 512px;
    background: linear-gradient(180deg, var(--card-top) 0%, var(--card-top-edge) 100%);
    box-shadow: 0 18px 40px rgba(30, 40, 55, 0.18);
    overflow: hidden;
  }
  .brand-name {
    position: absolute;
    left: 0;
    right: 0;
    top: 118px;
    text-align: center;
    font-family: "Open Sans", sans-serif;
    font-weight: 400;
    font-size: 72px;
    color: var(--wordmark);
    line-height: 1;
  }
  .info-band {
    position: absolute;
    left: 0;
    top: 318px;
    width: 900px;
    height: 194px;
    background: linear-gradient(180deg, var(--band-light) 0%, var(--band-dark) 100%);
  }
  .band-rule {
    position: absolute;
    left: 0;
    top: 306px;
    width: 900px;
    height: 36px;
  }
  .contact-list {
    position: absolute;
    left: 62px;
    top: 362px;
    list-style: none;
  }
  .contact-item {
    display: flex;
    align-items: center;
    height: 35px;
    font-size: 21px;
    font-weight: 400;
    color: var(--text-light);
    white-space: nowrap;
  }
  .contact-icon {
    width: 20px;
    height: 20px;
    margin-right: 14px;
    flex: none;
    fill: var(--icon-light);
  }
  .person {
    position: absolute;
    right: 62px;
    top: 392px;
    text-align: right;
    white-space: nowrap;
  }
  .person-name {
    font-size: 27px;
    font-weight: 600;
    color: var(--name-gold);
    line-height: 1.25;
  }
  .person-title {
    font-size: 22px;
    font-weight: 400;
    color: var(--text-light);
    line-height: 1.35;
  }
</style>
</head>
<body>
<div class="canvas">
  <section class="business-card">
    <div class="brand-name">quilmora</div>

    <div class="info-band"></div>
    <svg class="band-rule" viewBox="0 0 900 36" aria-hidden="true">
      <polygon points="0,8 739,8 752,28 765,8 900,8 900,14 769,14 752,36 735,14 0,14" fill="#2b2d2f"/>
    </svg>

    <ul class="contact-list">
      <li class="contact-item">
        <svg class="contact-icon" viewBox="0 0 24 24" aria-hidden="true">
          <path d="M3 8c0-3 4-5 9-5s9 2 9 5v2h-5V8c-1-1-7-1-8 0v2H3z"/>
          <path d="M7 12h10l3 8H4z"/>
        </svg>
        (800) 471-2960
      </li>
      <li class="contact-item">
        <svg class="contact-icon" viewBox="0 0 24 24" aria-hidden="true">
          <path d="M2 6h20v1.5l-10 6.5L2 7.5z"/>
          <path d="M2 9.5l10 6.5 10-6.5V18H2z"/>
        </svg>
        sleep@quilmora.com
      </li>
      <li class="contact-item">
        <svg class="contact-icon" viewBox="0 0 24 24" aria-hidden="true">
          <circle cx="12" cy="12" r="10"/>
          <path d="M12 2v20M2 12h20M5 6c4 2 10 2 14 0M5 18c4-2 10-2 14 0" stroke="#1f6ea3" stroke-width="1.4" fill="none"/>
        </svg>
        www.quilmora.com
      </li>
    </ul>

    <div class="person">
      <div class="person-name">Devin Holt</div>
      <div class="person-title">President</div>
    </div>
  </section>
</div>
</body>
</html>
```